Website to design and sell sundials: www.gnomonvale.com

We have a website that creates a free paper sundial, we want to migrate from this not profit free website to a website where we will continue offering the free paper sundial model but We will also offer a manufactured sundial and sell it.
In order to understand the project, please visit:
http://www.gnomonvale.com/vertical/sundial.html and
http://www.torvel.net/landing/

The website user journey should be redesigned, including the phases that are,
select language
Show product give info
Creation/edit sundial (could be one or more phases)
View created sundial
Buy sundial.

May some of them could be combined or splitted, what It have more sense.

Requirements
Must have
• A description page user journey offering freemium paper sundial and physical sundial to sell.
• A sundial creation page for "free" paper sundial
• A result page for paper sundial
• A sell page for physical

```html
<!DOCTYPE html>
<html lang="en">
<head>
<meta charset="utf-8">
<title>GnomonVale — Sundials</title>
<link href="https://fonts.googleapis.com/css2?family=Raleway:wght@400;500;600;700&display=swap" rel="stylesheet">
<style>
:root{
  --red:#b8120f;
  --orange:#f9b03b;
  --dark:#4b4b4b;
  --text:#444;
  --rule:#dcdcdc;
  --footer:#f1f1f1;
}
*{box-sizing:border-box;margin:0;padding:0}
html,body{width:823px;height:1200px;overflow:hidden;background:#fff}
body{font-family:'Raleway',sans-serif;color:var(--text);position:relative}
.topbar{position:absolute;left:0;top:0;width:823px;height:3px;background:var(--red)}
.brand{position:absolute;display:flex;align-items:center;gap:6px;color:var(--red);font-weight:600;white-space:nowrap}
.brand .dot{width:10px;height:10px;border-radius:50%;background:var(--orange)}
.brand--header{left:54px;top:36px;font-size:19px}
.nav{position:absolute;top:31px;left:333px;display:flex;align-items:center;font-size:10.5px;font-weight:500;color:#333;white-space:nowrap}
.nav a{color:inherit;text-decoration:none;margin-right:23px}
.nav a.active{color:var(--red)}
.nav .buy{background:var(--orange);color:#fff;padding:7px 12px;margin-right:25px}
.nav .lang{display:flex;align-items:center;gap:6px;font-size:10px}
.flag{width:15px;height:10px;background:#2b3e8c;border:1px solid #ccc}
.hero{position:absolute;left:51px;top:79px;width:722px;height:238px}
.hero-panel{position:absolute;left:0;top:0;width:247px;height:238px;background:var(--orange);padding:18px 18px 0;color:#fff}
.hero-panel::after{content:"";position:absolute;right:-19px;top:26px;border-left:19px solid var(--orange);border-top:17px solid transparent;border-bottom:17px solid transparent;z-index:2}
.hero-panel h1{color:var(--red);font-size:21px;font-weight:600;margin-bottom:8px}
.hero-panel p{font-size:9.6px;line-height:18.4px}
.btn-more{position:absolute;left:15px;top:190px;width:95px;height:29px;background:var(--dark);color:#fff;font-size:11.5px;display:flex;align-items:center;justify-content:center}
.hero-photo{position:absolute;left:247px;top:0;width:475px;height:238px;background:linear-gradient(135deg,#4e5a22,#2f3814 60%,#5a6628)}
.dots{position:absolute;left:283px;top:208px;display:flex;gap:6px}
.dots span{width:10px;height:10px;border-radius:50%;background:#fff}
.dots span:first-child{background:var(--red)}
.section-title{position:absolute;left:0;width:823px;text-align:center;color:var(--red);font-weight:500}
.steps{position:absolute;top:393px;left:40px;display:flex}
.step{width:149px;text-align:center}
.step .num{width:32px;height:32px;margin:0 auto 12px;border-radius:50%;border:2px solid var(--red);background:var(--orange);color:#fff;font-weight:700;font-size:12px;display:flex;align-items:center;justify-content:center}
.step h3{color:var(--red);font-size:10px;font-weight:600;margin-bottom:2px}
.step p{font-size:9.6px;line-height:16px;padding:0 15px}
.gallery{position:absolute;top:530px;left:51px;display:flex;gap:20px}
.gallery .frame{width:227px;height:199px;border:1px solid var(--rule);padding:2px}
.gallery .fill{width:100%;height:100%}
.fill--template{background:linear-gradient(160deg,#fff,#f3eeee)}
.fill--wall{background:linear-gradient(120deg,#b96a50,#a15640 55%,#d9d6cf)}
.fill--plate{background:radial-gradient(circle at 55% 45%,#d9dae8 0 30%,#46521e 60%)}
.divider{position:absolute;left:51px;top:757px;width:722px;height:1px;background:var(--rule)}
.samples{position:absolute;top:827px;left:51px;display:flex;gap:18px}
.sample{width:167px;text-align:center}
.sample .thumb{height:111px;border:1px solid var(--rule);background:linear-gradient(180deg,#fff,#f4f4f4)}
.sample h4{margin-top:14px;font-size:10.5px;font-weight:600;color:#333;white-space:nowrap}
.btn-buy{position:absolute;left:281px;top:1045px;width:252px;height:38px;background:var(--orange);border:1px solid var(--red);color:#fff;font-weight:700;font-size:15px;display:flex;align-items:center;justify-content:center;gap:9px}
.footer{position:absolute;left:0;top:1114px;width:823px;height:86px;background:var(--footer)}
.footer .brand{left:54px;top:23px;font-size:14px}
.copy{position:absolute;left:52px;top:51px;font-size:8.5px;white-space:nowrap}
.footer-heading{position:absolute;top:20px;font-size:10.5px;font-weight:500;color:var(--text);white-space:nowrap}
.footer-heading--pay{left:396px}
.footer-heading--social{left:651px}
.cards{position:absolute;left:396px;top:42px;display:flex;gap:6px}
.cards span{width:32px;height:19px;border-radius:2px}
.social{position:absolute;left:651px;top:40px;display:flex;gap:5px}
.social span{width:24px;height:24px}
</style>
</head>
<body>
<div class="topbar"></div>

<div class="brand brand--header"><span class="dot"></span>GnomonVale.com</div>
<nav class="nav">
  <a class="active">Home</a><a>Product</a><a>How it Works</a><a>Sundail Samples</a>
  <a class="buy">Buy Sundia</a>
  <span class="lang"><span class="flag"></span>EN
    <svg width="8" height="6" viewBox="0 0 8 6"><path d="M1 1l3 3 3-3" fill="none" stroke="#666"/></svg></span>
</nav>

<section class="hero">
  <div class="hero-panel">
    <h1>About Product</h1>
    <p>This page is about Sundials. Sundials are instruments that tell you the time with the shadow of the sun. To design a sundial you need to know exactly where you are going to put it, i.e. you need to know the longitude, the latitude and the orientation of the wall with respect to North.</p>
    <div class="btn-more">More Info</div>
  </div>
  <div class="hero-photo" role="img" aria-label="Photo of a metal sundial plate lying on grass">
    <div class="dots"><span></span><span></span><span></span></div>
  </div>
</section>

<h2 class="section-title" style="top:345px;font-size:22px">Creation/Edit Sundial</h2>
<div class="steps">
  <div class="step"><div class="num">1</div><h3>CALCULATE</h3><p>Fill in the form and create your sundial</p></div>
  <div class="step"><div class="num">2</div><h3>PRINT THE PDF</h3><p>To print, please select "shrink to page" in order not to deform the shape of the page.</p></div>
  <div class="step"><div class="num">3</div><h3>CUT AND FOLD</h3><p>Once you have your model printed, you have to cut (RED LINES), and fold (BLUE LINES).</p></div>
  <div class="step"><div class="num">4</div><h3>PUT ON YOUR WALL</h3><p>Put on your wall or Window</p></div>
  <div class="step"><div class="num">5</div><h3>ENJOY</h3></div>
</div>

<div class="gallery">
  <div class="frame"><div class="fill fill--template" role="img" aria-label="Printed paper sundial template with red cut lines and blue fold lines"></div></div>
  <div class="frame"><div class="fill fill--wall" role="img" aria-label="Paper sundial mounted on a brick wall"></div></div>
  <div class="frame"><div class="fill fill--plate" role="img" aria-label="Manufactured metal sundial on grass"></div></div>
</div>

<div class="divider"></div>

<h2 class="section-title" style="top:782px;font-size:22px">Created Sundial</h2>
<div class="samples">
  <div class="sample"><div class="thumb" role="img" aria-label="Sundial template for the southern hemisphere"></div><h4>South Hemisphere Buenos Aires</h4></div>
  <div class="sample"><div class="thumb" role="img" aria-label="Sundial template facing south east"></div><h4>Valencia South East</h4></div>
  <div class="sample"><div class="thumb" role="img" aria-label="Sundial template facing north west"></div><h4>Valencia NORTH WEST</h4></div>
  <div class="sample"><div class="thumb" role="img" aria-label="Sundial template facing west"></div><h4>Valencia WEST</h4></div>
</div>

<h2 class="section-title" style="top:1008px;font-size:16.5px;font-weight:600">Order Your Sundial Today</h2>
<div class="btn-buy">
  <svg width="15" height="13" viewBox="0 0 15 13"><path d="M0 1h3l2 7h8l2-6H4" fill="none" stroke="#fff" stroke-width="1.8"/><circle cx="6" cy="11" r="1.4" fill="#fff"/><circle cx="12" cy="11" r="1.4" fill="#fff"/></svg>
  BUY SUNDIAL
</div>

<footer class="footer">
  <div class="brand"><span class="dot"></span>GnomonVale.com</div>
  <p class="copy">Copyright © 2016. All Right Reserved. Terms Of Uses</p>
  <h5 class="footer-heading footer-heading--pay">We Accepted</h5>
  <div class="cards">
    <span style="background:#e6e6e6"></span><span style="background:#2a5aa8"></span><span style="background:#c8242b"></span><span style="background:#5b8ec9"></span><span style="background:#f0f0f0;border:1px solid #ddd"></span>
  </div>
  <h5 class="footer-heading footer-heading--social">Follow Us</h5>
  <div class="social"><span style="background:#3b5998"></span><span style="background:#29a9e1"></span></div>
</footer>
</body>
</html>
```